Web Site Design and Business Card design for Recruiting Company

There are three major tasks in this project:
1) I need to re-design my newly created website www.talvoro.net using the same logo but creating a totally different recruiting template that will apply better for a recruitment site. I want to use the elements of the Talvoro Network logo (which is the road junction) and red, black and gray colors throughout the website. I need someone to both design and launch the site...
2) I would also like to design a double sided business card using the same logo/colors and elements as described above
3) I would also like to have a small thumbnail logo created. As our large logo cannot be previewed easily on the Pelmwork or on Google Chrome tab images

The design should be contemporary, minimalist and slick

```html
<!DOCTYPE html>
<html lang="en">
<head>
<meta charset="utf-8">
<title>Talvoro Network — Recruiting</title>
<link href="https://fonts.googleapis.com/css2?family=Open+Sans:wght@400;600;700&family=Roboto:wght@400;500;700&display=swap" rel="stylesheet">
<style>
:root{
  --red:#ff0000;
  --red-deep:#e30613;
  --ink:#1a1a1a;
  --text:#333333;
  --muted:#555555;
  --light:#f2f2f2;
  --line:#dddddd;
  --footer:#242424;
  --white:#ffffff;
}
*{box-sizing:border-box;margin:0;padding:0}
html,body{width:1200px;height:3719px;overflow:hidden;background:var(--white)}
body{font-family:"Roboto",sans-serif;color:var(--text)}
.page{position:relative;width:1200px;height:3719px;overflow:hidden}
.abs{position:absolute}

/* header */
.brand{left:123px;top:7px;width:180px;height:120px;display:flex;align-items:center;gap:10px}
.brand-mark{width:18px;height:18px;border-radius:50%;background:var(--red)}
.brand-name{font-family:"Open Sans",sans-serif;font-weight:600;font-size:24px;color:var(--ink)}
.call{left:693px;top:18px;display:flex;align-items:center;gap:12px}
.call-icon{width:46px;height:46px;border:2px solid var(--red);border-radius:50%;display:flex;align-items:center;justify-content:center}
.call small{display:block;font-size:15px;color:var(--text);line-height:1}
.call strong{display:block;font-size:21px;font-weight:500;color:var(--ink);line-height:1.2}
.search-box{left:946px;top:17px;width:143px;height:36px;border:1px solid #ccc;border-radius:18px;font-size:15px;color:#777;padding:8px 12px;display:flex;justify-content:space-between;align-items:center}
.nav{left:693px;top:88px;display:flex;gap:38px;font-size:15px;font-weight:500;color:var(--ink)}
.nav .active{color:var(--red)}

/* hero */
.hero{left:0;top:133px;width:1200px;height:586px;background:radial-gradient(circle at 68% 45%,#1f56c9 0%,#0d2a8a 28%,#08175a 55%,#050d36 100%)}
.hero-title{left:107px;top:280px;font-family:"Open Sans",sans-serif;font-weight:700;font-size:62px;color:var(--white);letter-spacing:1px}
.hero-sub{left:111px;top:363px;font-size:15px;line-height:25px;color:var(--white);width:400px}
.select{top:442px;height:37px;width:161px;background:var(--white);border-radius:19px;display:flex;align-items:center;justify-content:space-between;padding:0 14px;font-size:14px;color:var(--ink)}
.select span{display:flex;align-items:center;gap:7px}
.hero-search{left:257px;top:503px;width:233px;height:39px;background:var(--red);border-radius:20px;color:var(--white);font-size:14px;display:flex;align-items:center;justify-content:space-between;padding:0 22px}
.dot-arrow{top:645px;width:31px;height:31px;border:1.5px solid var(--white);border-radius:50%;display:flex;align-items:center;justify-content:center}

/* about */
.about-red{left:826px;top:820px;width:374px;height:429px;background:var(--red)}
.about-photo{left:654px;top:853px;width:441px;height:364px;background:linear-gradient(135deg,#6f6a63,#3f4a4a 45%,#b9b2a8)}
.about-kicker{left:101px;top:870px;font-family:"Open Sans",sans-serif;font-size:26px;color:var(--ink)}
.about-title{left:101px;top:902px;font-family:"Open Sans",sans-serif;font-weight:600;font-size:30px;color:var(--ink)}
.rule{height:3px;background:var(--red)}
.about-text{left:101px;top:993px;width:422px;font-family:"Open Sans",sans-serif;font-size:15px;line-height:26px;text-align:justify;color:var(--text)}
.btn-red{background:var(--red);color:var(--white);font-family:"Open Sans",sans-serif;font-weight:600;display:flex;align-items:center;justify-content:center}

/* services */
.services-band{left:0;top:1352px;width:1200px;height:283px;background:linear-gradient(180deg,#1b1b1b,#2a2a2a 60%,#111)}
.gray-zone{left:0;top:1635px;width:1200px;height:941px;background:var(--light)}
.section-title{width:1200px;left:0;text-align:center;font-family:"Open Sans",sans-serif;font-weight:600;font-size:31px}
.card{top:1525px;width:277px;height:350px;background:var(--white);border-radius:138px 138px 0 0/68px 68px 0 0;box-shadow:0 3px 8px rgba(0,0,0,.08)}
.card-icon{position:absolute;left:98px;top:22px}
.card h3{position:absolute;top:125px;width:100%;text-align:center;font-family:"Open Sans",sans-serif;font-weight:600;font-size:14px;color:var(--ink)}
.card ul{position:absolute;top:165px;left:22px;list-style:none}
.card li{display:flex;align-items:center;gap:12px;font-size:15px;line-height:32.5px;color:#444}

/* jobs */
.job{left:113px;width:974px;height:84px}
.job-badge{position:absolute;left:0;top:0;width:81px;height:81px;border:2px solid var(--ink);border-radius:50%;display:flex;align-items:center;justify-content:center;background:var(--white)}
.job-text{position:absolute;left:91px;top:8px;width:320px;font-family:"Open Sans",sans-serif;font-size:15.5px;line-height:24.5px;color:var(--text)}
.job-loc{position:absolute;left:744px;top:25px;display:flex;align-items:center;gap:14px;font-family:"Open Sans",sans-serif;font-size:15.5px;color:var(--text)}
.job-btn{position:absolute;left:811px;top:76px;width:142px;height:43px;font-size:15px;font-weight:400}

/* news */
.news{width:480px;height:199px;background:var(--white);box-shadow:0 2px 10px rgba(0,0,0,.12);display:flex}
.news-photo{width:209px;height:199px;flex:none}
.news-body{padding:22px 22px 0 23px;font-family:"Open Sans",sans-serif}
.news-date{color:var(--red);font-size:15px}
.news-head{margin-top:14px;font-weight:600;font-size:15px;color:var(--ink)}
.news-text{margin-top:9px;font-size:15px;line-height:22px;color:var(--text)}
.news-more{margin-top:11px;display:flex;align-items:center;gap:6px;color:var(--red);font-weight:700;font-size:15px}

/* footer */
.footer{left:0;top:3304px;width:1200px;height:415px;background:var(--footer);color:var(--white);font-family:"Open Sans",sans-serif}
.footer .c{position:absolute;width:1200px;text-align:center}
.nl-input{left:339px;top:120px;width:387px;height:52px;background:var(--white);color:#333;font-size:15px;padding:16px 18px}
.nl-btn{left:726px;top:120px;width:136px;height:52px;font-size:15px}
.footer-rule{left:111px;top:205px;width:976px;height:1px;background:#444}
.footer-nav{top:240px;left:0;width:1200px;display:flex;justify-content:center;gap:42px;font-size:15px;font-weight:600}
.socials{top:300px;left:0;width:1200px;display:flex;justify-content:center;gap:21px}
.socials span{width:22px;height:22px;border-radius:50%;background:var(--white)}
</style>
</head>
<body>
<div class="page">

  <!-- header -->
  <div class="abs brand"><span class="brand-mark"></span><span class="brand-name">Talvoro</span></div>
  <div class="abs call">
    <div class="call-icon"><svg width="22" height="22" viewBox="0 0 24 24" fill="none" stroke="#ff0000" stroke-width="1.6"><path d="M5 3h4l2 5-2.5 1.5a11 11 0 0 0 6 6L16 13l5 2v4a2 2 0 0 1-2 2A16 16 0 0 1 3 5a2 2 0 0 1 2-2z"/></svg></div>
    <div><small>CALL US</small><strong>+1-404-555-0192</strong></div>
  </div>
  <div class="abs search-box">Search <svg width="13" height="13" viewBox="0 0 24 24" fill="none" stroke="#333" stroke-width="3"><circle cx="10" cy="10" r="7"/><path d="M15 15l6 6"/></svg></div>
  <nav class="abs nav"><span class="active">HOME</span><span>ABOUT US</span><span>SERVICES</span><span>CONTACT US</span></nav>

  <!-- hero -->
  <div class="abs hero" role="img" aria-label="Glowing blue globe with a network of connected people"></div>
  <h1 class="abs hero-title">TALVORO</h1>
  <p class="abs hero-sub">Talvoro Network LLC is an Atlanta based talent advisory, recruiting and staffing firm</p>
  <div class="abs select" style="left:113px"><span><svg width="16" height="16" viewBox="0 0 24 24" fill="none" stroke="#222" stroke-width="2"><path d="M4 20h16M5 4h9v2M4 4v16M16 4l4 4-9 9H7v-4z"/></svg>JOB TITLE</span><svg width="12" height="8" viewBox="0 0 12 8" fill="none" stroke="#222" stroke-width="1.6"><path d="M1 1l5 5 5-5"/></svg></div>
  <div class="abs select" style="left:293px"><span><svg width="12" height="16" viewBox="0 0 12 16"><path d="M6 0a6 6 0 0 0-6 6c0 4.5 6 10 6 10s6-5.5 6-10a6 6 0 0 0-6-6zm0 8.5A2.5 2.5 0 1 1 6 3.5a2.5 2.5 0 0 1 0 5z" fill="#222"/></svg>LOCATION</span><svg width="12" height="8" viewBox="0 0 12 8" fill="none" stroke="#222" stroke-width="1.6"><path d="M1 1l5 5 5-5"/></svg></div>
  <div class="abs select" style="left:472px"><span><svg width="16" height="14" viewBox="0 0 16 14" fill="none" stroke="#222" stroke-width="1.5"><rect x="1" y="3" width="14" height="10" rx="1"/><path d="M5 3V1h6v2M1 7h14"/></svg>JOB TYPE</span><svg width="12" height="8" viewBox="0 0 12 8" fill="none" stroke="#222" stroke-width="1.6"><path d="M1 1l5 5 5-5"/></svg></div>
  <div class="abs hero-search">SEARCH <svg width="15" height="15" viewBox="0 0 24 24" fill="none" stroke="#fff" stroke-width="2.6"><circle cx="10" cy="10" r="7"/><path d="M15 15l6 6"/></svg></div>
  <div class="abs dot-arrow" style="left:586px"><svg width="8" height="12" viewBox="0 0 8 12" fill="none" stroke="#fff" stroke-width="1.6"><path d="M7 1L2 6l5 5"/></svg></div>
  <div class="abs dot-arrow" style="left:629px"><svg width="8" height="12" viewBox="0 0 8 12" fill="none" stroke="#fff" stroke-width="1.6"><path d="M1 1l5 5-5 5"/></svg></div>

  <!-- about -->
  <div class="abs about-red"></div>
  <div class="abs about-photo" role="img" aria-label="Smiling recruiter in an interview meeting in an office"></div>
  <div class="abs about-kicker">ABOUT</div>
  <h2 class="abs about-title">TALVORO</h2>
  <div class="abs rule" style="left:101px;top:968px;width:93px"></div>
  <p class="abs about-text">Talvoro Network LLC is an Atlanta based talent advisory, recruiting and staffing firm. We help companies find skilled professionals within the shortest time frames though our unique network of business and personal connections nationwide and overseas. of business and personal connections nationwide and overseas</p>
  <div class="abs btn-red" style="left:103px;top:1177px;width:132px;height:42px;font-size:15px">READ MORE</div>

  <!-- services -->
  <div class="abs services-band" role="img" aria-label="Dark office background"></div>
  <div class="abs gray-zone"></div>
  <h2 class="abs section-title" style="top:1407px;color:var(--white)">OUR SERVICES</h2>
  <div class="abs rule" style="left:570px;top:1465px;width:64px"></div>

  <div class="abs card" style="left:172px">
    <svg class="card-icon" width="80" height="86" viewBox="0 0 80 86" fill="none" stroke="#e30613" stroke-width="2.4"><rect x="4" y="24" width="72" height="46" rx="2"/><path d="M30 80h20M40 70v10M20 6h34l8 8v40H20z"/><path d="M28 22h16M28 32h26M28 42h26"/></svg>
    <h3>INFORMATION TECHNOLOGY (IT)</h3>
    <ul>
      <li><svg width="17" height="12" viewBox="0 0 17 12" fill="none" stroke="#ff0000" stroke-width="1.8"><path d="M0 6h15M10 1l5 5-5 5"/></svg>Project Management</li>
      <li><svg width="17" height="12" viewBox="0 0 17 12" fill="none" stroke="#ff0000" stroke-width="1.8"><path d="M0 6h15M10 1l5 5-5 5"/></svg>Network Administration</li>
      <li><svg width="17" height="12" viewBox="0 0 17 12" fill="none" stroke="#ff0000" stroke-width="1.8"><path d="M0 6h15M10 1l5 5-5 5"/></svg>Software Engineering</li>
      <li><svg width="17" height="12" viewBox="0 0 17 12" fill="none" stroke="#ff0000" stroke-width="1.8"><path d="M0 6h15M10 1l5 5-5 5"/></svg>Technical Support</li>
      <li><svg width="17" height="12" viewBox="0 0 17 12" fill="none" stroke="#ff0000" stroke-width="1.8"><path d="M0 6h15M10 1l5 5-5 5"/></svg>Quality Assurance</li>
    </ul>
  </div>
  <div class="abs card" style="left:464px">
    <svg class="card-icon" width="86" height="86" viewBox="0 0 86 86" fill="none" stroke="#e30613" stroke-width="2.4"><rect x="4" y="4" width="30" height="24" rx="4"/><circle cx="26" cy="50" r="10"/><circle cx="60" cy="14" r="10"/><path d="M8 84V72a14 10 0 0 1 28 0v12M42 40a14 10 0 0 1 28 0v8M48 54h32v22H48z"/></svg>
    <h3>TELECOMMUNICATIONS</h3>
    <ul>
      <li><svg width="17" height="12" viewBox="0 0 17 12" fill="none" stroke="#ff0000" stroke-width="1.8"><path d="M0 6h15M10 1l5 5-5 5"/></svg>Site Acquisition</li>
      <li><svg width="17" height="12" viewBox="0 0 17 12" fill="none" stroke="#ff0000" stroke-width="1.8"><path d="M0 6h15M10 1l5 5-5 5"/></svg>Cell Site Integration</li>
      <li><svg width="17" height="12" viewBox="0 0 17 12" fill="none" stroke="#ff0000" stroke-width="1.8"><path d="M0 6h15M10 1l5 5-5 5"/></svg>Site Maintenance</li>
      <li><svg width="17" height="12" viewBox="0 0 17 12" fill="none" stroke="#ff0000" stroke-width="1.8"><path d="M0 6h15M10 1l5 5-5 5"/></svg>Project Support</li>
      <li><svg width="17" height="12" viewBox="0 0 17 12" fill="none" stroke="#ff0000" stroke-width="1.8"><path d="M0 6h15M10 1l5 5-5 5"/></svg>Construction Management</li>
    </ul>
  </div>
  <div class="abs card" style="left:755px">
    <svg class="card-icon" width="84" height="86" viewBox="0 0 84 86" fill="none" stroke="#e30613" stroke-width="2.4"><rect x="4" y="4" width="60" height="78" rx="3"/><rect x="12" y="12" width="44" height="16"/><path d="M12 38h12v10H12zM30 38h12v10H30zM48 38h8v10h-8zM12 56h12v10H12zM30 56h12v10H30zM74 8v70M70 8h8"/></svg>
    <h3>ACCOUNTING &amp; FINANCE</h3>
    <ul>
      <li><svg width="17" height="12" viewBox="0 0 17 12" fill="none" stroke="#ff0000" stroke-width="1.8"><path d="M0 6h15M10 1l5 5-5 5"/></svg>Financial Planning</li>
      <li><svg width="17" height="12" viewBox="0 0 17 12" fill="none" stroke="#ff0000" stroke-width="1.8"><path d="M0 6h15M10 1l5 5-5 5"/></svg>Financial Management</li>
      <li><svg width="17" height="12" viewBox="0 0 17 12" fill="none" stroke="#ff0000" stroke-width="1.8"><path d="M0 6h15M10 1l5 5-5 5"/></svg>Audit</li>
      <li><svg width="17" height="12" viewBox="0 0 17 12" fill="none" stroke="#ff0000" stroke-width="1.8"><path d="M0 6h15M10 1l5 5-5 5"/></svg>Cost Accounting</li>
      <li><svg width="17" height="12" viewBox="0 0 17 12" fill="none" stroke="#ff0000" stroke-width="1.8"><path d="M0 6h15M10 1l5 5-5 5"/></svg>Payroll</li>
    </ul>
  </div>

  <!-- recent jobs -->
  <h2 class="abs section-title" style="top:1973px;color:var(--ink)">RECENT JOBS</h2>
  <div class="abs rule" style="left:547px;top:2027px;width:79px"></div>

  <div class="abs job" style="top:2090px">
    <div class="job-badge"><svg width="40" height="40" viewBox="0 0 40 40" fill="none" stroke="#e30613" stroke-width="2"><circle cx="20" cy="20" r="14"/><path d="M10 22l6 6 14-14"/></svg></div>
    <p class="job-text">Sed ut perspiciatis unde omnis iste natus error sit voluptatem accusantium doloremque</p>
    <div class="job-loc"><svg width="14" height="19" viewBox="0 0 12 16"><path d="M6 0a6 6 0 0 0-6 6c0 4.5 6 10 6 10s6-5.5 6-10a6 6 0 0 0-6-6zm0 8.5A2.5 2.5 0 1 1 6 3.5a2.5 2.5 0 0 1 0 5z" fill="#111"/></svg>Lorem ipsum dolor sit amet</div>
    <div class="btn-red job-btn">FULL TIME</div>
  </div>
  <div class="abs job" style="top:2236px">
    <div class="job-badge"><svg width="40" height="40" viewBox="0 0 40 40" fill="none" stroke="#e30613" stroke-width="2"><rect x="8" y="8" width="24" height="26"/><path d="M13 14h4M23 14h4M13 20h4M23 20h4M13 26h4M23 26h4M4 34h32"/></svg></div>
    <p class="job-text">Sed ut perspiciatis unde omnis iste natus error sit voluptatem accusantium doloremque</p>
    <div class="job-loc"><svg width="14" height="19" viewBox="0 0 12 16"><path d="M6 0a6 6 0 0 0-6 6c0 4.5 6 10 6 10s6-5.5 6-10a6 6 0 0 0-6-6zm0 8.5A2.5 2.5 0 1 1 6 3.5a2.5 2.5 0 0 1 0 5z" fill="#111"/></svg>Lorem ipsum dolor sit amet</div>
    <div class="btn-red job-btn">PART TIME</div>
  </div>
  <div class="abs job" style="top:2382px">
    <div class="job-badge"><svg width="40" height="40" viewBox="0 0 40 40" fill="none" stroke="#e30613" stroke-width="2"><circle cx="12" cy="12" r="5"/><circle cx="28" cy="12" r="5"/><circle cx="12" cy="28" r="5"/><circle cx="28" cy="28" r="5"/><path d="M17 12h6M17 28h6M12 17v6M28 17v6"/></svg></div>
    <p class="job-text">Sed ut perspiciatis unde omnis iste natus error sit voluptatem accusantium doloremque</p>
    <div class="job-loc"><svg width="14" height="19" viewBox="0 0 12 16"><path d="M6 0a6 6 0 0 0-6 6c0 4.5 6 10 6 10s6-5.5 6-10a6 6 0 0 0-6-6zm0 8.5A2.5 2.5 0 1 1 6 3.5a2.5 2.5 0 0 1 0 5z" fill="#111"/></svg>Lorem ipsum dolor sit amet</div>
    <div class="btn-red job-btn">FULL TIME</div>
  </div>

  <!-- latest news -->
  <h2 class="abs section-title" style="top:2673px;color:var(--ink)">LATEST NEWS</h2>
  <div class="abs rule" style="left:570px;top:2725px;width:60px"></div>

  <article class="abs news" style="left:111px;top:2787px">
    <div class="news-photo" role="img" aria-label="Two businessmen in suits talking" style="background:linear-gradient(135deg,#d9d9d9,#4a4a4a 55%,#c9c9c9)"></div>
    <div class="news-body"><div class="news-date">8TH JULY 2019</div><div class="news-head">NEMO ENIM VOLUPTATEM</div><div class="news-text">Sed ut perspiciatis unde omnis iste natus error sit voluptatem accusantium laudantium</div><div class="news-more">READ MORE <svg width="14" height="14" viewBox="0 0 14 14" fill="none" stroke="#ff0000" stroke-width="1.5"><circle cx="7" cy="7" r="6"/><path d="M6 4l3 3-3 3"/></svg></div></div>
  </article>
  <article class="abs news" style="left:608px;top:2787px">
    <div class="news-photo" role="img" aria-label="Businesswoman in a blazer" style="background:linear-gradient(135deg,#eeeeee,#8a8580 50%,#2f2f2f)"></div>
    <div class="news-body"><div class="news-date">8TH JULY 2019</div><div class="news-head">NEMO ENIM VOLUPTATEM</div><div class="news-text">Sed ut perspiciatis unde omnis iste natus error sit voluptatem accusantium laudantium</div><div class="news-more">READ MORE <svg width="14" height="14" viewBox="0 0 14 14" fill="none" stroke="#ff0000" stroke-width="1.5"><circle cx="7" cy="7" r="6"/><path d="M6 4l3 3-3 3"/></svg></div></div>
  </article>
  <article class="abs news" style="left:111px;top:3002px">
    <div class="news-photo" role="img" aria-label="Hand touching a network of people icons" style="background:linear-gradient(135deg,#3e3a5a,#7c7897 50%,#4a3d4f)"></div>
    <div class="news-body"><div class="news-date">8TH JULY 2019</div><div class="news-head">NEMO ENIM VOLUPTATEM</div><div class="news-text">Sed ut perspiciatis unde omnis iste natus error sit voluptatem accusantium laudantium</div><div class="news-more">READ MORE <svg width="14" height="14" viewBox="0 0 14 14" fill="none" stroke="#ff0000" stroke-width="1.5"><circle cx="7" cy="7" r="6"/><path d="M6 4l3 3-3 3"/></svg></div></div>
  </article>
  <article class="abs news" style="left:608px;top:3002px">
    <div class="news-photo" role="img" aria-label="Business handshake in a bright office" style="background:linear-gradient(135deg,#e8eef2,#9aa7b0 50%,#5a6b5a)"></div>
    <div class="news-body"><div class="news-date">8TH JULY 2019</div><div class="news-head">NEMO ENIM VOLUPTATEM</div><div class="news-text">Sed ut perspiciatis unde omnis iste natus error sit voluptatem accusantium laudantium</div><div class="news-more">READ MORE <svg width="14" height="14" viewBox="0 0 14 14" fill="none" stroke="#ff0000" stroke-width="1.5"><circle cx="7" cy="7" r="6"/><path d="M6 4l3 3-3 3"/></svg></div></div>
  </article>

  <!-- footer -->
  <footer class="abs footer">
    <div class="c" style="top:47px;font-size:15px;font-weight:600">SIGNUP FOR NEWSLETTER</div>
    <div class="c" style="top:73px;font-size:15px">We will never share your email address width third-party</div>
    <div class="abs nl-input">Enter your email</div>
    <div class="abs btn-red nl-btn">SUBSCRIBE</div>
    <div class="abs footer-rule"></div>
    <div class="abs footer-nav"><span>HOME</span><span>ABOUT US</span><span>SERVICES</span><span>CONTACT US</span></div>
    <div class="abs socials" aria-label="Social links"><span></span><span></span><span></span><span></span><span></span></div>
    <div class="c" style="top:355px;font-size:15px">copyrights © 2019 All Rights Reserved</div>
  </footer>

</div>
</body>
</html>
```